We are a recruitment company based in Norwich/Cambridge England.
I have included our company logo which we want to remain the same.

What we are looking for is a new creative Business card which will really stand out!!

Contact Information for Business Card

Harriet Dunmore
email: Harriet@plavex.co.uk
Address: Brackwell House
Fenmoor Enterprise Park
Partridge Way
Norwich
QB9 3KX
Tel:01632 960418

```html
<!DOCTYPE html>
<html lang="en">
<head>
<meta charset="utf-8">
<title>Plavex Business Card</title>
<link href="https://fonts.googleapis.com/css2?family=Arimo:wght@400;700&display=swap" rel="stylesheet">
<style>
  :root {
    --backdrop: #2b2b2d;
    --card: #1d1d1f;
    --green: #8dc63f;
    --grey: #8e8b90;
    --text-light: #c9c9cc;
  }
  * { margin: 0; padding: 0; box-sizing: border-box; }
  html, body {
    width: 1200px; height: 1189px; overflow: hidden;
    background: var(--backdrop);
    font-family: "Arimo", Arial, sans-serif;
  }
  .card {
    position: absolute; left: 150px;
    width: 900px; height: 514px;
    background: var(--card);
    border-radius: 28px;
    overflow: hidden;
    box-shadow: 0 10px 30px rgba(0,0,0,.45);
  }
  .card--front { top: 40px; }
  .card--back { top: 630px; }

  .brand { display: flex; align-items: center; gap: 18px; }
  .brand__dot { width: 64px; height: 64px; border-radius: 50%; background: var(--grey); }
  .brand__name { font-weight: 700; color: var(--green); letter-spacing: -1px; line-height: 1; }

  .card--front .brand { position: absolute; left: 50%; top: 50%; transform: translate(-50%, -50%); }
  .card--front .brand__name { font-size: 96px; }
  .card--front .brand__dot { width: 78px; height: 78px; }

  .card--back .brand { position: absolute; left: 70px; top: 60px; }
  .card--back .brand__name { font-size: 80px; }

  .rule { position: absolute; left: 80px; right: 50px; top: 318px; height: 2px; background: var(--green); }

  .person { position: absolute; left: 90px; top: 276px; }
  .person__name { color: var(--green); font-weight: 700; font-size: 34px; line-height: 38px; }
  .person__role { position: absolute; top: 46px; left: 0; color: var(--grey); font-size: 24px; line-height: 26px; }

  .contacts { position: absolute; left: 90px; top: 362px; list-style: none; }
  .contacts li { display: flex; align-items: center; gap: 14px; color: var(--text-light); font-size: 25px; height: 33px; }
  .contacts svg { width: 26px; height: 26px; flex: none; }

  .address { position: absolute; right: 60px; top: 332px; text-align: right; color: var(--text-light); font-size: 22px; line-height: 30px; }

  .band { position: absolute; left: 0; bottom: 0; width: 900px; height: 130px; }
</style>
</head>
<body>
  <section class="card card--front">
    <div class="brand">
      <span class="brand__dot"></span>
      <span class="brand__name">Plavex</span>
    </div>
  </section>

  <section class="card card--back">
    <div class="brand">
      <span class="brand__dot"></span>
      <span class="brand__name">Plavex</span>
    </div>

    <div class="rule"></div>

    <div class="person">
      <p class="person__name">Harriet Dunmore</p>
      <p class="person__role">CEO</p>
    </div>

    <ul class="contacts">
      <li>
        <svg viewBox="0 0 26 26"><circle cx="13" cy="13" r="12" fill="none" stroke="#8dc63f" stroke-width="1.5"/><rect x="9" y="6" width="8" height="14" rx="1.5" fill="none" stroke="#8dc63f" stroke-width="1.5"/></svg>
        01632 960418
      </li>
      <li>
        <svg viewBox="0 0 26 26"><circle cx="13" cy="13" r="12" fill="none" stroke="#8dc63f" stroke-width="1.5"/><rect x="7" y="8.5" width="12" height="9" fill="none" stroke="#8dc63f" stroke-width="1.5"/><path d="M7 8.5 L13 14 L19 8.5" fill="none" stroke="#8dc63f" stroke-width="1.5"/></svg>
        Harriet@plavex.co.uk
      </li>
      <li>
        <svg viewBox="0 0 26 26"><circle cx="13" cy="13" r="12" fill="none" stroke="#8dc63f" stroke-width="1.5"/><circle cx="13" cy="13" r="7" fill="none" stroke="#8dc63f" stroke-width="1.3"/><ellipse cx="13" cy="13" rx="3" ry="7" fill="none" stroke="#8dc63f" stroke-width="1.3"/><path d="M6 13 H20" stroke="#8dc63f" stroke-width="1.3"/></svg>
        www.plavex.co.uk
      </li>
    </ul>

    <p class="address">Brackwell House, Fenmoor Enterprise Park<br>Partridge Way, Norwich QB9 3KX</p>

    <svg class="band" viewBox="0 0 900 130" aria-hidden="true">
      <path d="M0 90 H560 L578 20 H588 L570 98 H0 Z" fill="#8e8b90"/>
      <path d="M0 104 H574 L596 26 H900 V130 H0 Z" fill="#8dc63f"/>
    </svg>
  </section>
</body>
</html>
```